Leap Past Harvest Moon 21 day Challenge

We are having a Leap Past Harvest Moon Challenge at our fitness studio. We need a poster design using the template attached as a reference. I have also included our Zorbelle logo to put on the poster. Please DO NOT use the graphics in the flyer as we are expecting something much better :-)

-Size needed 11x17 with bleeding for printing

-We need this made in Photoshop (CS3 friendly) or at least delivered in PS as we might change some text or re-arrange the design later on.

-We need this in layers.

Fitness

```html
<!DOCTYPE html>
<html lang="en">
<head>
<meta charset="utf-8">
<title>Leap Past Harvest Moon Challenge – Zorbelle Bootcamps</title>
<link rel="stylesheet" href="https://fonts.googleapis.com/css2?family=Arimo:wght@700&family=Damion&family=Zilla+Slab:wght@500;700&display=swap">
<style>
  :root {
    --cream: #f7dfbb;
    --title-cream: #f4dcb6;
    --rust: #a8693a;
    --ink: #333333;
    --white: #ffffff;
    --sky: #4f95dd;
    --bullet: #f3e27a;
  }
  * { margin: 0; padding: 0; box-sizing: border-box; }
  html, body { width: 796px; height: 1200px; overflow: hidden; background: var(--cream); }
  .poster { position: relative; width: 796px; height: 1200px; background: var(--cream); font-family: "Arimo", Arial, sans-serif; font-weight: 700; }
  .card { position: absolute; left: 57px; top: 60px; width: 683px; height: 1080px; background: var(--rust); border-radius: 42px; overflow: hidden; }
  .center { position: absolute; left: 0; width: 100%; text-align: center; display: block; }
  h1 { font-weight: 400; }

  .title-script { font-family: "Damion", cursive; color: var(--title-cream); font-size: 132px; line-height: 1; top: 78px; }
  .title-joiner { top: 195px; color: var(--title-cream); font-family: "Damion", cursive; font-size: 40px; line-height: 1; display: flex; justify-content: center; align-items: center; gap: 14px; }
  .title-joiner::before, .title-joiner::after { content: ""; width: 80px; height: 5px; background: var(--title-cream); }
  .title-slab { top: 240px; font-family: "Zilla Slab", Georgia, serif; font-weight: 500; font-size: 122px; line-height: 1; letter-spacing: 4px; color: var(--title-cream); }
  .title-moon { top: 372px; display: flex; justify-content: center; align-items: center; gap: 18px; font-family: "Damion", cursive; font-size: 66px; line-height: 1; color: var(--title-cream); }
  .title-moon::before, .title-moon::after { content: ""; width: 120px; height: 5px; background: var(--title-cream); }

  .headline { top: 487px; font-size: 27px; line-height: 35px; color: var(--ink); }
  .benefits { position: absolute; left: 104px; top: 570px; width: 552px; list-style: none; color: var(--white); font-size: 15px; line-height: 17px; }
  .benefits li { position: relative; padding-left: 14px; }
  .benefits li::before { content: ""; position: absolute; left: 0; top: 6px; width: 7px; height: 7px; border-radius: 50%; background: var(--bullet); }
  .value { top: 668px; font-size: 29px; line-height: 34px; color: var(--ink); }
  .price { top: 700px; display: flex; justify-content: center; align-items: center; gap: 6px; font-size: 38px; line-height: 44px; color: var(--white); }
  .price::before, .price::after { content: ""; width: 130px; height: 4px; background: var(--ink); }
  .quote { top: 754px; font-size: 19px; line-height: 24px; color: var(--white); }
  .quote-author { top: 782px; font-size: 12px; color: var(--ink); }

  .brand { top: 858px; display: flex; justify-content: center; align-items: center; gap: 12px; font-size: 46px; line-height: 56px; color: var(--ink); }
  .brand-mark { width: 24px; height: 24px; background: var(--ink); }

  .cta-band { position: absolute; left: 0; bottom: 0; width: 100%; height: 142px; background: var(--sky); border-top: 5px solid var(--ink); }
  .cta { top: 18px; font-size: 20px; line-height: 30px; color: var(--ink); }
</style>
</head>
<body>
<div class="poster">
  <main class="card">
    <h1>
      <span class="center title-script">Leap</span>
      <span class="center title-joiner">past</span>
      <span class="center title-slab">HARVEST</span>
      <span class="center title-moon">Moon</span>
    </h1>

    <p class="center headline">DISCOVER THE SECRET TO A<br>FALL-READY BODY IN JUST 21 DAYS!</p>

    <ul class="benefits">
      <li>9 total training sessions designed to incinerate fat off your midsection, thighs, and arms</li>
      <li>21 days of nutritional guidance, including delicious recipes</li>
      <li>A Success Session to map out your individual plan for success</li>
      <li>Your very own Personal Accountability Coach to ensure you get results</li>
    </ul>

    <p class="center value">YOU GET ALL THIS—A $399 VALUE</p>
    <p class="center price">FOR ONLY $99!</p>

    <p class="center quote">I've never been more fit in my life—at age 41!</p>
    <p class="center quote-author">~Marisol Quenby</p>

    <div class="center brand"><span class="brand-mark"></span><span>Zorbelle</span></div>

    <section class="cta-band">
      <p class="center cta">HURRY! SPACE IS LIMITED TO ONLY 20 PARTICIPANTS!!!<br>CLAIM YOUR SPOT NOW</p>
    </section>
  </main>
</div>
</body>
</html>
```